business card for a massage therapy practice named 'Cedar and Willow Massage Studio'

I really need a trendy, yet easy on the eyes business card to complement my logo. Ideally with some gold or rose gold foil work.

My uploaded file of the logo I have in horizontal but I have a vertical version as well. Another color that is used in the website is a blush pink here and there. I'd like to see some trendy tropical leaves in the design.

```html
<!DOCTYPE html>
<html lang="en">
<head>
<meta charset="utf-8">
<title>Cedar and Willow Massage Studio — Business Card</title>
<link rel="stylesheet" href="https://fonts.googleapis.com/css2?family=Kaushan+Script&family=Tinos&display=swap">
<style>
  :root {
    --backdrop: #8c8c8c;
    --card-black: #1e1e1e;
    --card-white: #ffffff;
    --gold: #c9a23a;
    --gold-light: #f1dc6a;
    --gold-deep: #b8901f;
    --ink: #141414;
  }
  html, body {
    margin: 0;
    padding: 0;
    width: 865px;
    height: 1200px;
    overflow: hidden;
    background: var(--backdrop);
  }
  .canvas {
    position: relative;
    width: 865px;
    height: 1200px;
  }
  .card {
    position: absolute;
    left: 82px;
    width: 700px;
    height: 400px;
    box-shadow: 0 6px 18px rgba(0,0,0,0.35);
    overflow: hidden;
  }
  .card--front {
    top: 150px;
    background: var(--card-black);
  }
  .card--back {
    top: 650px;
    background: var(--card-white);
  }
  .brand {
    position: absolute;
    display: flex;
    align-items: center;
    gap: 18px;
    font-family: "Kaushan Script", cursive;
    line-height: 1;
    white-space: nowrap;
  }
  .brand__dot {
    width: 22px;
    height: 22px;
    border-radius: 50%;
    flex: none;
  }
  .card--front .brand {
    left: 0;
    right: 0;
    top: 160px;
    justify-content: center;
    font-size: 40px;
    color: var(--gold);
  }
  .card--front .brand__dot { background: var(--gold); }
  .card--back .brand {
    left: 70px;
    top: 70px;
    font-size: 38px;
    color: var(--ink);
  }
  .card--back .brand__dot { background: var(--ink); }
  .foil-band {
    position: absolute;
    left: 0;
    right: 0;
    top: 190px;
    height: 176px;
    background: linear-gradient(100deg, var(--gold-deep) 0%, var(--gold-light) 30%, var(--gold) 55%, var(--gold-light) 80%, var(--gold-deep) 100%);
  }
  .foil-stripe {
    position: absolute;
    left: 0;
    right: 0;
    top: 376px;
    height: 24px;
    background: linear-gradient(100deg, var(--gold-deep), var(--gold-light) 50%, var(--gold-deep));
  }
  .contact {
    position: absolute;
    left: 0;
    right: 0;
    top: 212px;
    text-align: center;
    color: var(--ink);
  }
  .contact__name {
    font-family: "Kaushan Script", cursive;
    font-size: 30px;
    margin: 0 0 10px;
  }
  .contact__line {
    font-family: "Tinos", serif;
    font-size: 15px;
    margin: 0 0 4px;
  }
</style>
</head>
<body>
<main class="canvas">
  <section class="card card--front" aria-label="Business card front">
    <div class="brand">
      <span class="brand__dot"></span>
      <span class="brand__name">Cedar &amp; Willow Massage Studio</span>
    </div>
  </section>

  <section class="card card--back" aria-label="Business card back">
    <div class="brand">
      <span class="brand__dot"></span>
      <span class="brand__name">Cedar &amp; Willow Massage Studio</span>
    </div>
    <div class="foil-band"></div>
    <div class="foil-stripe"></div>
    <div class="contact">
      <p class="contact__name">Daniel Moon</p>
      <p class="contact__line">+822-5550-1234</p>
      <p class="contact__line">info@cedarandwillow.com | www.cedarandwillow.com</p>
      <p class="contact__line">5/F, Maple Hall, 120 Hanbit-ro, Seocho-gu, Seoul, 06500 Korea</p>
    </div>
  </section>
</main>
</body>
</html>
```